Harbor Crest Holdings Corporate Showcase

Provide an attractive Corporate Website for a boutique Investment Company to showcase our activities and corporate interests.

Our Company works across a number of Sectors including

Real Estate
E-Commerce
Healthcare
Beauty & Personal Care
Technology
Resources

Lets keep the personality

Modern
Global
Sophisticated
Calm
Interesting

Lets keep the pages with MINIMAL Words
Lets use Photos/ Imagery to tell the story

We'll need a Banner Menu -
About Us
Expertise
Global Outlook
Sectors
Management
Media
Contact Us

Many thanks
Best wishes
Dennis.

Target Market(s)

Investors
Clients

Coding

Coded - Design and coding required

Number of Pages Required

5+ page

Font styles to use
Sans Serif

Colors
886aae
3176b5
00a990
f68e4d
f04a50
e667a6

Requirements
Must have
• WordPress Coding

Checkout this Website for look and feel - its cool:
www.qvr-example.com

Harbor Crest Partners
(Harbor Crest Holdings LLP)
London
E9 4ZX
United Kingdom

www.HarborCrestPartners-example.com
Nice to have
• Sophisticated colour palette - black/ brown/ blue/ purple/

```html
<!DOCTYPE html>
<html lang="en">
<head>
<meta charset="utf-8">
<title>Harbor Crest Holdings</title>
<link href="https://fonts.googleapis.com/css2?family=Nunito:wght@400;600;700&family=Saira:wght@400&family=Montserrat:wght@600;700&family=Open+Sans:wght@700&display=swap" rel="stylesheet">
<style>
:root{
  --navy:#0e1c2b;
  --teal:#18a07f;
  --purple:#6d4fa0;
  --red:#ec3341;
  --grey-bg:#efefef;
  --text:#333;
  --muted:#777;
  --line:#cfcfcf;
  --pink:#df4f98;
  --blue:#2a60ad;
}
*{box-sizing:border-box;margin:0;padding:0}
html,body{width:1200px;height:3568px;overflow:hidden}
body{position:relative;font-family:'Nunito',sans-serif;color:var(--text);background:#fff}
.abs{position:absolute}
.btn{position:absolute;background:var(--red);color:#fff;font-family:'Montserrat',sans-serif;font-weight:600;font-size:16px;display:flex;align-items:center;justify-content:center;text-transform:uppercase}
.topbar{left:0;top:0;width:1200px;height:64px;background:rgba(10,22,32,.85);z-index:3}
.brand{position:absolute;left:143px;top:12px;font-family:'Saira',sans-serif;font-size:31px;color:#fff}
.hero{left:0;top:0;width:1200px;height:700px}
.hero-title{left:144px;top:254px;font-family:'Montserrat',sans-serif;font-weight:700;font-size:38px;line-height:48px;color:#fff}
.section-title{width:1200px;text-align:center;font-size:32px;color:var(--purple);font-weight:600}
.welcome-text{left:144px;top:812px;width:912px;text-align:center;font-size:16.5px;line-height:32px;color:#444}
.grey{left:0;width:1200px;background:var(--grey-bg)}
.big-heading{font-family:'Open Sans',sans-serif;font-weight:700;font-size:80px;color:#7b7b7b;letter-spacing:-1px}
.expertise-text{left:144px;top:1207px;width:350px;font-size:16.5px;line-height:32px;color:#444}
.card{position:absolute;width:250px;height:272px;color:#fff;padding:18px 16px}
.card h3{position:absolute;left:16px;top:122px;font-weight:600;font-size:19px}
.card p{position:absolute;left:16px;top:156px;width:220px;font-size:11.5px;line-height:19px}
.card .go{position:absolute;left:16px;top:226px}
.sector{position:absolute;width:287px;text-align:center;font-size:20px;color:#333}
.sector svg{display:block;margin:0 auto 8px}
.vline{position:absolute;width:1px;background:var(--line)}
.hline{position:absolute;height:2px;background:#ddd;width:287px}
.media-card{position:absolute;top:2492px;width:296px;height:297px;background:#fff;box-shadow:0 2px 6px rgba(0,0,0,.1);padding:9px}
.media-card .ph{height:128px}
.media-card .date{color:var(--red);font-size:16px;margin:18px 0 0 9px}
.media-card p{margin:8px 9px 0;font-size:15.5px;line-height:24px;color:#333}
.field{position:absolute;border:1px solid #bbb;background:#fff;font-size:14px;color:#999;padding:14px 20px}
.footer-links{left:0;top:3474px;width:1200px;text-align:center;font-size:11.5px;color:#d6dde4}
.footer-links span{margin:0 8px}
.copy{left:0;top:3506px;width:1200px;text-align:center;font-size:11.5px;color:#d6dde4}
</style>
</head>
<body>

<svg class="abs hero" width="1200" height="700" role="img" aria-label="Hand holding a tablet with a rising green stock chart on a dark teal background">
  <defs>
    <linearGradient id="heroGrad" x1="0" y1="0" x2="1" y2="1">
      <stop offset="0" stop-color="#0f2a36"/>
      <stop offset=".55" stop-color="#1a4b55"/>
      <stop offset="1" stop-color="#0d2230"/>
    </linearGradient>
  </defs>
  <polygon points="0,686 600,686 0,600" fill="#fff"/>
  <polygon points="0,600 600,686 1200,600 1200,618 600,688 0,618" fill="var(--teal)"/>
  <polygon points="0,0 1200,0 1200,600 600,670 0,600" fill="url(#heroGrad)"/>
  <polyline points="610,280 660,260 700,255 740,230 780,200 820,160 850,120 872,92" fill="none" stroke="#2ad4a0" stroke-width="3" opacity=".7"/>
  <path d="M60,318 l-12,12 l12,12" fill="none" stroke="#fff" stroke-width="4"/>
  <path d="M1128,318 l12,12 l-12,12" fill="none" stroke="#fff" stroke-width="4"/>
</svg>

<div class="abs topbar">
  <div class="brand">Harbor Crest Holdings</div>
  <svg class="abs" style="left:964px;top:18px" width="30" height="30"><circle cx="12" cy="12" r="9" fill="none" stroke="#fff" stroke-width="2.5"/><line x1="19" y1="19" x2="27" y2="27" stroke="#fff" stroke-width="3"/></svg>
  <svg class="abs" style="left:1020px;top:20px" width="36" height="24"><rect y="1" width="36" height="3" fill="#fff"/><rect y="8" width="36" height="3" fill="#fff"/><rect y="15" width="36" height="3" fill="#fff"/><rect y="21" width="36" height="2" fill="#fff"/></svg>
</div>

<div class="abs hero-title">PROIN EGET CONGUE<br>VEL TEMPOR DIAM</div>
<div class="btn" style="left:144px;top:366px;width:128px;height:47px">Read More</div>

<svg class="abs" style="left:0;top:870px" width="142" height="352"><path d="M0,0 C50,20 140,110 140,170 C140,250 70,320 0,350 Z" fill="var(--pink)"/></svg>

<div class="abs section-title" style="top:760px">Welcome to Harbor Crest Holdings</div>
<div class="abs welcome-text">Aenean facilisis tincidunt lectus, id dictum nisi luctus eget. Vivamus efficitur ex condimentum, malesuada eros eget, feugiat nibh. Sed tellus ex, imperdiet eget gravida sit amet, volutpat eget turpis. In nec ultricies est. Etiam mattis augue vehicula odio posuere, sit amet tempus lectus luctus. Etiam vel massa elementum, bibendum tellus venenatis.</div>
<div class="btn" style="left:536px;top:919px;width:128px;height:47px">Read More</div>

<div class="abs grey" style="top:1046px;height:727px"></div>
<svg class="abs" style="left:0;top:1046px" width="142" height="176"><path d="M0,0 L120,0 C140,60 100,140 0,174 Z" fill="var(--pink)"/></svg>
<div class="abs big-heading" style="left:140px;top:1108px">Expertise</div>
<div class="abs expertise-text">Vivamus lacus justo, ultrices nec erat euismod iaculis mauris. Vivamus eleifend vitae nulla vel malesuada. In ac malesuada lacus, et consectetur ante. Fusce vitae lectus sit amet mi pulvinar maximus.</div>
<div class="btn" style="left:144px;top:1383px;width:128px;height:47px">Read More</div>
<div class="abs" style="left:104px;top:1469px;width:374px;height:291px;background:radial-gradient(ellipse at 50% 50%,#e2e4e8 0%,#ececec 55%,rgba(239,239,239,0) 75%)" role="img" aria-label="Smartphone showing a colourful pie chart and data rows"></div>

<div class="card" style="left:535px;top:1128px;background:linear-gradient(135deg,#6a4ea0,#2f64ae)">
  <svg width="86" height="80" fill="none" stroke="#fff" stroke-width="2"><rect x="4" y="4" width="36" height="52" rx="3"/><rect x="10" y="10" width="24" height="10"/><circle cx="30" cy="60" r="12"/><rect x="44" y="18" width="22" height="30"/><line x1="48" y1="26" x2="62" y2="26"/><line x1="48" y1="34" x2="62" y2="34"/><line x1="56" y1="70" x2="78" y2="44"/></svg>
  <h3>Nulla facilisi</h3>
  <p>Maecenas vel tortor accumsan quam varius imperdiet vel eget elit. Aenean facilisis tincidunt lectus.</p>
  <svg class="go" width="22" height="22"><circle cx="11" cy="11" r="10" fill="#fff"/><path d="M7,11 h7 M11,7 l4,4 l-4,4" stroke="#3f5aa8" stroke-width="2.5" fill="none"/></svg>
</div>
<div class="card" style="left:805px;top:1128px;background:linear-gradient(135deg,#7e55ac,#e0539e)">
  <svg width="86" height="80" fill="none" stroke="#fff" stroke-width="2"><circle cx="30" cy="30" r="22"/><circle cx="30" cy="30" r="14"/><line x1="46" y1="46" x2="70" y2="70"/><line x1="60" y1="20" x2="76" y2="6"/><circle cx="8" cy="58" r="2"/></svg>
  <h3>Etiam quis</h3>
  <p>Maecenas consequat justo enim, ac mattis massa imperdiet quis. Fusce eget neque elit. Sed augue orci.</p>
  <svg class="go" width="22" height="22"><circle cx="11" cy="11" r="10" fill="#fff"/><path d="M7,11 h7 M11,7 l4,4 l-4,4" stroke="#b04fa5" stroke-width="2.5" fill="none"/></svg>
</div>
<div class="card" style="left:535px;top:1421px;background:linear-gradient(135deg,#ec3549,#f4813a)">
  <svg width="86" height="80" fill="none" stroke="#fff" stroke-width="2"><rect x="6" y="6" width="44" height="60"/><rect x="14" y="2" width="44" height="60"/><circle cx="36" cy="30" r="12"/><path d="M36,30 v-12 M36,30 h12"/><line x1="20" y1="50" x2="50" y2="50"/></svg>
  <h3>Duis ornare</h3>
  <p>Fusce sollicitudin lorem et luctus volutpat. Proin placerat dapibus gravida tristique tristique nulla eget hendrerit.</p>
  <svg class="go" width="22" height="22"><circle cx="11" cy="11" r="10" fill="#fff"/><path d="M7,11 h7 M11,7 l4,4 l-4,4" stroke="#ee5441" stroke-width="2.5" fill="none"/></svg>
</div>
<div class="card" style="left:805px;top:1421px;background:linear-gradient(135deg,#2a5fae,#12a886)">
  <svg width="86" height="80" fill="none" stroke="#fff" stroke-width="2"><circle cx="24" cy="24" r="18"/><path d="M24,24 v-12"/><rect x="50" y="8" width="24" height="6"/><rect x="50" y="20" width="24" height="6"/><rect x="4" y="50" width="16" height="20"/><path d="M30,70 v-14 M40,70 v-20 M50,70 v-26 M60,70 v-32"/></svg>
  <h3>Aliquam erat</h3>
  <p>ellentesque convallis molestie enim sit amet efficitur. Etiam id imperdiet lectus. Vivamus lacus justo.</p>
  <svg class="go" width="22" height="22"><circle cx="11" cy="11" r="10" fill="#fff"/><path d="M7,11 h7 M11,7 l4,4 l-4,4" stroke="#1b8a9a" stroke-width="2.5" fill="none"/></svg>
</div>

<div class="abs section-title" style="top:1846px">Sectors</div>
<div class="vline" style="left:443px;top:1910px;height:125px"></div>
<div class="vline" style="left:755px;top:1910px;height:125px"></div>
<div class="hline" style="left:144px;top:2060px"></div>
<div class="hline" style="left:456px;top:2060px"></div>
<div class="hline" style="left:768px;top:2060px"></div>
<div class="vline" style="left:443px;top:2086px;height:125px"></div>
<div class="vline" style="left:755px;top:2086px;height:125px"></div>

<div class="sector" style="left:144px;top:1924px"><svg width="60" height="58" fill="none" stroke="#333" stroke-width="2"><path d="M4,28 L30,6 L56,28"/><rect x="10" y="26" width="40" height="28"/><rect x="24" y="38" width="12" height="16"/><rect x="14" y="32" width="8" height="8"/><rect x="38" y="32" width="8" height="8"/></svg>Real Estate</div>
<div class="sector" style="left:456px;top:1924px"><svg width="60" height="58" fill="none" stroke="#333" stroke-width="2"><path d="M4,4 h8 l6,34 h32 l6,-24 h-40"/><circle cx="24" cy="50" r="4"/><circle cx="44" cy="50" r="4"/></svg>E-Commerce</div>
<div class="sector" style="left:768px;top:1924px"><svg width="60" height="58" fill="none" stroke="#333" stroke-width="2"><rect x="18" y="4" width="24" height="18"/><path d="M30,8 v10 M25,13 h10"/><rect x="6" y="22" width="48" height="32"/><rect x="24" y="40" width="12" height="14"/><rect x="12" y="28" width="8" height="8"/><rect x="40" y="28" width="8" height="8"/></svg>Healthcare</div>
<div class="sector" style="left:144px;top:2108px"><svg width="60" height="58" fill="none" stroke="#333" stroke-width="2"><rect x="16" y="6" width="28" height="40" rx="14"/><line x1="30" y1="46" x2="30" y2="54"/><line x1="20" y1="54" x2="40" y2="54"/></svg>Beauty &amp; Personal Care</div>
<div class="sector" style="left:456px;top:2108px"><svg width="60" height="58" fill="none" stroke="#333" stroke-width="2"><path d="M50,4 C34,6 22,18 18,34 l8,8 C42,38 54,26 56,10 Z"/><circle cx="40" cy="20" r="5"/><path d="M18,34 l-10,2 l8,-12 M26,42 l-2,10 l12,-8"/><path d="M14,44 l-8,8"/></svg>Technology</div>
<div class="sector" style="left:768px;top:2108px"><svg width="60" height="58" fill="none" stroke="#333" stroke-width="2"><rect x="6" y="28" width="30" height="16" rx="8" transform="rotate(-45 21 36)"/><rect x="24" y="14" width="30" height="16" rx="8" transform="rotate(-45 39 22)"/></svg>Resources</div>

<div class="abs grey" style="top:2314px;height:566px"></div>
<svg class="abs" style="left:1055px;top:2140px" width="145" height="350"><path d="M145,0 C80,20 0,100 0,190 C0,260 80,320 145,348 Z" fill="var(--blue)"/></svg>
<div class="abs big-heading" style="left:140px;top:2376px">Media</div>
<div class="btn" style="left:927px;top:2405px;width:128px;height:47px">View All</div>

<div class="media-card" style="left:144px"><div class="ph" role="img" aria-label="Laptop displaying trading charts" style="background:linear-gradient(135deg,#1b2150,#2f3a7a 60%,#151a3a)"></div><div class="date">15 DECEMBER, 2020</div><p>Fusce vitae lectus sit amet mi pulvinar maximus. Aenean placerat, nibh vel accumsan aliquet, magna nibh accumsan nibh.</p></div>
<div class="media-card" style="left:452px"><div class="ph" role="img" aria-label="Hourglass, globe and coins on a table" style="background:linear-gradient(180deg,#d6d8da,#8f9499 70%,#5a6066)"></div><div class="date">15 DECEMBER, 2020</div><p>Donec vestibulum odio sem, laoreet massa ullamcorper id. Donec molestie ni tellus hendrerit vehicula. Nunc eu ligula sed.</p></div>
<div class="media-card" style="left:760px"><div class="ph" role="img" aria-label="Hands counting banknotes beside a calculator" style="background:linear-gradient(135deg,#c9a27a,#e4d3b8 55%,#9b7a5a)"></div><div class="date">15 DECEMBER, 2020</div><p>Proin porta fermentum ipsum, vel turpis venenatis luctus. Vivamus volutpat eu sapien quis tempus. Aenean feugiat viverra</p></div>

<div class="abs section-title" style="top:2950px">Contact Us</div>
<div class="field" style="left:144px;top:3007px;width:448px;height:48px">Name</div>
<div class="field" style="left:144px;top:3071px;width:448px;height:48px">Email</div>
<div class="field" style="left:144px;top:3135px;width:448px;height:48px">Phone Number</div>
<div class="field" style="left:607px;top:3007px;width:448px;height:176px">Message</div>
<div class="btn" style="left:536px;top:3203px;width:128px;height:47px">Submit</div>

<svg class="abs" style="left:0;top:3320px" width="1200" height="248">
  <polygon points="0,96 600,6 1200,96 1200,248 0,248" fill="var(--teal)"/>
  <polygon points="0,102 600,18 1200,102 1200,248 0,248" fill="var(--navy)"/>
  <circle cx="568" cy="105" r="21" fill="none" stroke="#c8d0d8" stroke-width="1.5"/>
  <circle cx="632" cy="105" r="21" fill="none" stroke="#c8d0d8" stroke-width="1.5"/>
</svg>
<div class="abs footer-links">Home<span>|</span>About Us<span>|</span>Expertise<span>|</span>Global Outlook<span>|</span>Sectors<span>|</span>Management<span>|</span>Media<span>|</span>Contact Us</div>
<div class="abs copy">Copyright &copy; 2020 &nbsp; Harbor Crest Holdings. All rights reserved.</div>

</body>
</html>
```